EB-5 Regional Center needs a Web design

Harlow Ridge Financial Partners is an expanding EB-r regional center. We have been successful in sponsoring multiple projects of third-party developers and placing EB-5, B-1, and Private Investments into multiple projects.

We are now partnering directly with project developers in the energy and healthcare to raise foreign capital for projects in those industries. The foreign capital is used as project equity and our collective balance sheets are used to guarantee debt to complete the funding of the projects.

We need a web site where we can post our company credentials, the bios of each partner, a document page for each of our projects where we can post specific project related documents which foreign investors can read, and we will need a section where foreign investors can fill out investor forms confirming that they are qualified investors and leaving their contact so that our agents and executives can make contact.

The final design should reflect the exceptional experience of the partners and our financial strength and stability.

We do have a logo we would want to use on the web design.

Target Market(s)

EB-5 Investors, B-1 Investors, Private Equity and other investors seeking quality investment in job creating US projects.

Coding

Number of Pages Required

5+ page

Font styles to use
Sans Serif

Requirements
Must have
• Pages to display company info, partner bios, projects completed, and a projects in-process page where we can post documents and info on projects for which we are seeking foreign investment. We also need a section where investors can enter their qualifying personal information and leave contact information for us.

```html
<!DOCTYPE html>
<html lang="en">
<head>
<meta charset="utf-8">
<title>Harlow Ridge Financial Partners</title>
<link rel="stylesheet" href="https://fonts.googleapis.com/css2?family=Roboto:wght@400;500;700;900&family=Open+Sans:wght@400;600&family=Montserrat:wght@400&display=swap">
<style>
:root{
  --navy:#0b2c48;
  --navy-deep:#082640;
  --steel:#2a6b99;
  --slate:#56677a;
  --ink:#222;
  --muted:#555;
  --white:#fff;
  --line:#ddd;
}
*{box-sizing:border-box;margin:0;padding:0}
html,body{width:1200px;height:3301px;overflow:hidden}
body{position:relative;font-family:"Roboto",sans-serif;color:var(--ink);background:var(--white)}
.abs{position:absolute}

/* top bar */
.topbar{left:0;top:0;width:1200px;height:49px;background:var(--navy-deep);color:var(--white);font-family:"Open Sans",sans-serif;font-size:17px}
.topbar .item{position:absolute;top:13px;display:flex;align-items:center;gap:10px}
.topbar .sep{position:absolute;left:273px;top:10px;width:1px;height:30px;background:#8aa}
.social{display:flex;gap:12px}
.social span{width:33px;height:33px;border:2px solid currentColor;border-radius:50%;display:block}

/* nav */
.nav{left:0;top:49px;width:1200px;height:97px;background:var(--white)}
.brand{position:absolute;left:107px;top:30px;display:flex;align-items:center;gap:10px;color:var(--slate)}
.brand .mark{width:38px;height:38px;border-radius:50%;background:var(--slate)}
.brand .name{font-size:22px;font-weight:500;line-height:1}
.brand .name small{display:block;font-size:11px;letter-spacing:2px;font-weight:400;margin-top:3px}
.menu{position:absolute;left:409px;top:40px;display:flex;gap:30px;font-size:15px;color:#333}
.menu .active{color:var(--navy)}
.btn{display:inline-block;background:var(--navy);color:var(--white);border-radius:30px;font-family:"Open Sans",sans-serif;font-weight:600;text-align:center}
.quote{left:928px;top:77px;width:159px;height:48px;line-height:48px;font-size:17px}

/* hero */
.hero{left:0;top:146px;width:1200px;height:549px;background:linear-gradient(180deg,#8d8a66 0%,#b88a5c 55%,#a47358 100%);text-align:center;color:var(--white)}
.hero h1{position:absolute;top:158px;width:100%;font-size:41px;font-weight:700;text-shadow:0 2px 4px rgba(0,0,0,.4)}
.hero p{position:absolute;top:224px;width:100%;font-size:20px;line-height:30px;text-shadow:0 1px 3px rgba(0,0,0,.5)}
.hero .btn{position:absolute;left:516px;top:310px;width:168px;height:49px;line-height:49px;font-size:17px}
.dots{position:absolute;left:563px;top:509px;display:flex;gap:10px}
.dots i{width:7px;height:7px;border-radius:50%;background:var(--navy);display:block}

/* about */
.about-title{left:108px;top:770px;font-family:"Montserrat",sans-serif;font-size:35px;color:var(--navy)}
.rule{height:3px;background:var(--navy);border-radius:2px}
.about-text{left:108px;top:840px;width:515px;font-size:15px;line-height:34.5px;color:#333;text-align:justify}
.readmore{left:108px;top:1110px;width:168px;height:49px;line-height:49px;font-size:17px}
.about-block{left:718px;top:792px;width:395px;height:412px;background:var(--steel)}
.about-photo{left:683px;top:774px;width:395px;height:412px;background:linear-gradient(135deg,#c9b48f,#7c8a5a 50%,#8c8a80)}

/* projects */
.projects{left:0;top:1317px;width:1200px;height:711px;background:linear-gradient(180deg,#7a879b,#5c6a80);color:var(--white);text-align:center}
.projects h2{position:absolute;top:43px;width:100%;font-family:"Open Sans",sans-serif;font-size:38px;font-weight:600}
.projects .lead{position:absolute;left:200px;top:116px;width:800px;font-family:"Open Sans",sans-serif;font-size:17px;line-height:33px}
.pcard{position:absolute;top:231px;width:310px;height:407px;background:var(--white);color:var(--ink);overflow:hidden}
.pcard .ph{height:190px}
.pcard h3{margin-top:30px;font-size:19px;font-weight:700;color:var(--navy)}
.pcard p{margin:14px 22px 0;font-family:"Open Sans",sans-serif;font-size:17px;line-height:29px;color:#555}
.pcard svg{position:absolute;right:0;bottom:0}
.vdots{position:absolute;left:1114px;top:313px;display:flex;flex-direction:column;gap:6px}
.vdots i{width:12px;height:12px;border-radius:50%;background:var(--white);display:block}

/* bios */
.bios{left:0;top:2028px;width:1200px;height:697px;background-color:#fafafa;background-image:radial-gradient(#dcdcdc 1px,transparent 1px);background-size:7px 7px}
.bios h2{position:absolute;top:68px;width:100%;text-align:center;font-size:38px;font-weight:500;color:var(--navy)}
.bcard{position:absolute;top:219px;width:283px;height:333px;background:var(--white);border:1px solid #ddd;box-shadow:0 2px 5px rgba(0,0,0,.1);text-align:center}
.bcard svg{position:absolute;left:0;top:0}
.bcard .avatar{position:absolute;left:81px;top:-35px;width:120px;height:120px;border-radius:50%;border:3px solid var(--white);background:linear-gradient(180deg,#a9a9a9,#555);box-shadow:0 0 0 1px #999}
.bcard .nm{margin-top:122px;font-size:21px;font-weight:500;color:#666}
.bcard .role{margin-top:18px;font-size:21px;color:#222}
.bcard p{margin:24px 18px 0;font-size:15px;line-height:29px;color:#555}
.arrow{position:absolute;top:2420px}

/* contact */
.contact{left:0;top:2725px;width:1200px;height:409px;background:linear-gradient(90deg,#1b3c5c,#14395a);color:var(--white)}
.contact h3{position:absolute;left:169px;top:66px;font-size:27px;font-weight:700}
.crow{position:absolute;display:flex;align-items:flex-start;gap:20px;font-family:"Open Sans",sans-serif;font-size:20px;line-height:32px}
.crow .ic{width:52px;height:52px;border-radius:50%;background:var(--white);display:flex;align-items:center;justify-content:center;flex:none}
.appt{left:655px;top:2698px;width:385px;height:411px;background:var(--white)}
.appt-wing{top:2698px;width:0;height:0}
.appt h3{margin-top:42px;text-align:center;font-size:27px;font-weight:700;color:var(--navy)}
.field{position:absolute;left:32px;width:322px;height:60px;border:1px solid #ccc;padding:20px 28px;font-family:"Open Sans",sans-serif;font-size:16px;color:#444}
.submit{position:absolute;left:109px;top:330px;width:168px;height:49px;line-height:49px;font-size:18px}

/* footer */
.footer{left:0;top:3134px;width:1200px;height:167px;background:var(--white);text-align:center}
.footer .social{position:absolute;left:536px;top:32px;color:var(--navy)}
.footer .social span{width:32px;height:32px}
.fmenu{position:absolute;left:0;top:96px;width:100%;display:flex;justify-content:center;gap:30px;font-size:16px;color:#222}
.copy{position:absolute;top:136px;width:100%;font-size:17px;color:#222}
</style>
</head>
<body>

<header class="abs topbar">
  <div class="item" style="left:111px">
    <svg width="22" height="22" viewBox="0 0 24 24"><path fill="#fff" d="M6.6 10.8a15 15 0 006.6 6.6l2.2-2.2c.3-.3.7-.4 1-.2 1.1.4 2.3.6 3.6.6.6 0 1 .4 1 1V20c0 .6-.4 1-1 1A17 17 0 013 4c0-.6.4-1 1-1h3.5c.6 0 1 .4 1 1 0 1.3.2 2.5.6 3.6.1.3 0 .7-.2 1z"/></svg>
    888-888-8888
  </div>
  <div class="sep"></div>
  <div class="item" style="left:288px">
    <svg width="22" height="18" viewBox="0 0 24 18"><rect width="24" height="18" rx="2" fill="#fff"/><path d="M1 2l11 8 11-8" stroke="#082640" stroke-width="2" fill="none"/></svg>
    info@HarlowRidgeFinancial
  </div>
  <div class="social" style="position:absolute;left:959px;top:6px;color:#fff">
    <span></span><span></span><span></span>
  </div>
</header>

<nav class="abs nav">
  <div class="brand">
    <div class="mark"></div>
    <div class="name">HARLOW RIDGE<small>Financial Partners</small></div>
  </div>
  <div class="menu">
    <span class="active">Home</span><span>About</span><span>Service</span><span>Projects</span><span>Contact Us</span><span>Careers</span>
  </div>
</nav>
<a class="abs btn quote">GET A QUOTE</a>

<section class="abs hero" role="img" aria-label="Stacks of coins with a rising arrow">
  <h1>HARLOW RIDGE FINANCIAL PARTNERS</h1>
  <p>Lorem ipsum dolor sit amet, consectetur adipiscing elit,<br>sed do eiusmod tempor incididunt ut labore.</p>
  <a class="btn">GET STARTED</a>
  <div class="dots"><i></i><i></i><i></i></div>
</section>

<h2 class="abs about-title">About Us</h2>
<div class="abs rule" style="left:109px;top:815px;width:56px"></div>
<p class="abs about-text">Lorem ipsum dolor sit amet, consectetur adipiscing elit, sed do eiusmod tempor incididunt ut labore et dolore magna aliqua. Quis ipsum suspendisse ultrices gravida. Risus commodo viverra maecenas accumsan lacus vel facilisis. sed do eiusmod tempor incididunt ut labore et dolore magna aliqua. Quis ipsum suspendisse ultrices gravida. Risus commodo viverra maecenas accumsan lacus vel facilisis. sed do eiusmod tempor incididunt ut labore et dolore magna aliqua.</p>
<a class="abs btn readmore">READ MORE</a>
<div class="abs about-block"></div>
<div class="abs about-photo" role="img" aria-label="Hand placing coins beside a young plant growing from coins"></div>

<section class="abs projects">
  <h2>Our Projects</h2>
  <div class="rule" style="position:absolute;left:572px;top:94px;width:52px;background:#fff"></div>
  <p class="lead">Lorem ipsum dolor sit amet, consectetur adipiscing elit, sed do eiusmod tempor incididunt ut labore et dolore magna aliqua. Quis ipsum suspendisse ultrices gravid.</p>

  <article class="pcard" style="left:109px">
    <div class="ph" role="img" aria-label="Coin stack against a city skyline" style="background:linear-gradient(135deg,#5b7390,#2c3f5c)"></div>
    <h3>NEQUE PORRO QUISQUAM EST</h3>
    <p>Lorem ipsum dolor sit amet, consectetur adipiscing elit, sed do eiusmod tempor incididunt ut</p>
    <svg width="65" height="45"><polygon points="0,45 65,0 65,45" fill="#0b2c48"/><path d="M45 27h12M51 21v12" stroke="#fff" stroke-width="2.5"/></svg>
  </article>
  <article class="pcard" style="left:442px">
    <div class="ph" role="img" aria-label="Person with coffee reviewing charts on a tablet" style="background:linear-gradient(135deg,#4a3e36,#c9c6c2)"></div>
    <h3>LOREM IPSUM DOLOR</h3>
    <p>Lorem ipsum dolor sit amet, consectetur adipiscing elit, sed do eiusmod tempor incididunt ut</p>
    <svg width="65" height="45"><polygon points="0,45 65,0 65,45" fill="#0b2c48"/><path d="M45 27h12M51 21v12" stroke="#fff" stroke-width="2.5"/></svg>
  </article>
  <article class="pcard" style="left:774px">
    <div class="ph" role="img" aria-label="Businessman holding a tablet with a glowing growth chart" style="background:linear-gradient(135deg,#1d2d4a,#3a5a86)"></div>
    <h3>NEQUE PORRO QUISQUAM EST</h3>
    <p>Lorem ipsum dolor sit amet, consectetur adipiscing elit, sed do eiusmod tempor incididunt ut</p>
    <svg width="65" height="45"><polygon points="0,45 65,0 65,45" fill="#0b2c48"/><path d="M45 27h12M51 21v12" stroke="#fff" stroke-width="2.5"/></svg>
  </article>
  <div class="vdots"><i></i><i></i><i></i></div>
</section>

<section class="abs bios">
  <h2>Partner Bios</h2>
  <div class="rule" style="position:absolute;left:572px;top:127px;width:54px"></div>

  <article class="bcard" style="left:122px">
    <svg width="283" height="90"><path d="M0 0H95A60 60 0 00188 0H283C240 50 200 80 141 82 82 80 43 50 0 0Z" fill="#4a5d73"/></svg>
    <div class="avatar" role="img" aria-label="Partner portrait"></div>
    <div class="nm">NAME</div><div class="role">Neque porro</div>
    <p>Lorem ipsum dolor sit amet, consectetur adipiscing elit, sed do eiusmod tempor.</p>
  </article>
  <article class="bcard" style="left:455px">
    <svg width="283" height="90"><path d="M0 0H95A60 60 0 00188 0H283C240 50 200 80 141 82 82 80 43 50 0 0Z" fill="#4a5d73"/></svg>
    <div class="avatar" role="img" aria-label="Partner portrait"></div>
    <div class="nm">NAME</div><div class="role">Neque porro</div>
    <p>Lorem ipsum dolor sit amet, consectetur adipiscing elit, sed do eiusmod tempor .</p>
  </article>
  <article class="bcard" style="left:791px">
    <svg width="283" height="90"><path d="M0 0H95A60 60 0 00188 0H283C240 50 200 80 141 82 82 80 43 50 0 0Z" fill="#4a5d73"/></svg>
    <div class="avatar" role="img" aria-label="Partner portrait"></div>
    <div class="nm">NAME</div><div class="role">Neque porro</div>
    <p>Lorem ipsum dolor sit amet, consectetur adipiscing elit, sed do eiusmod tempor .</p>
  </article>
</section>
<svg class="arrow" style="left:65px" width="16" height="24"><path d="M12 3L4 12l8 9" stroke="#333" stroke-width="2" fill="none"/></svg>
<svg class="arrow" style="left:1103px" width="16" height="24"><path d="M4 3l8 9-8 9" stroke="#333" stroke-width="2" fill="none"/></svg>

<section class="abs contact">
  <h3>Contact us</h3>
  <div class="crow" style="left:160px;top:130px">
    <span class="ic"><svg width="18" height="24" viewBox="0 0 18 24"><path d="M9 0a9 9 0 00-9 9c0 7 9 15 9 15s9-8 9-15a9 9 0 00-9-9z" fill="#1b3c5c"/><circle cx="9" cy="9" r="3.5" fill="#fff"/></svg></span>
    <span style="margin-left:2px">Lorem ipsum dolor sit<br>amet, consectetur<br>adipiscing elit,</span>
  </div>
  <div class="crow" style="left:160px;top:243px;align-items:center">
    <span class="ic"><svg width="22" height="22" viewBox="0 0 24 24"><path fill="#1b3c5c" d="M6.6 10.8a15 15 0 006.6 6.6l2.2-2.2c.3-.3.7-.4 1-.2 1.1.4 2.3.6 3.6.6.6 0 1 .4 1 1V20c0 .6-.4 1-1 1A17 17 0 013 4c0-.6.4-1 1-1h3.5c.6 0 1 .4 1 1 0 1.3.2 2.5.6 3.6.1.3 0 .7-.2 1z"/></svg></span>
    <span>(888) 888-8888</span>
  </div>
  <div class="crow" style="left:160px;top:327px;align-items:center;gap:14px;font-size:18px">
    <span class="ic"><svg width="22" height="16" viewBox="0 0 24 18"><rect x="1" y="1" width="22" height="16" rx="2" stroke="#1b3c5c" stroke-width="2" fill="none"/><path d="M1 2l11 8 11-8" stroke="#1b3c5c" stroke-width="2" fill="none"/></svg></span>
    <span>info@HarlowRidgeFinancial</span>
  </div>
</section>
<svg class="abs" style="left:618px;top:2698px" width="460" height="28"><polygon points="37,0 0,28 37,28" fill="#4a5d73"/><polygon points="422,0 460,28 422,28" fill="#4a5d73"/></svg>
<div class="abs appt">
  <h3>Get An Appointment</h3>
  <div class="field" style="top:100px">Name</div>
  <div class="field" style="top:173px">Email</div>
  <div class="field" style="top:246px">Message</div>
  <a class="btn submit">SUBMIT</a>
</div>

<footer class="abs footer">
  <div class="social"><span></span><span></span><span></span></div>
  <div class="fmenu"><span>Home</span><span>About</span><span>Service</span><span>Projects</span><span>Contact Us</span><span>Careers</span></div>
  <div class="copy">Copyrights 2020 All rights reserved</div>
</footer>

</body>
</html>
```